Maple Gable Business Card

Colors can be blue, grey and white as you see in the attached logo. Needs to have a spot for name, title, phone, email, address, and website. There also needs to be a spot for an agent's picture.

Contact Information for Business Card

See project description.

Colors

Designer to choose colors to be used in the design.

```html
<!DOCTYPE html>
<html lang="en">
<head>
<meta charset="UTF-8">
<title>Maple Gable Business Card</title>
<link href="https://fonts.googleapis.com/css2?family=Montserrat:wght@400;500;600;700&display=swap" rel="stylesheet">
<style>
  :root {
    --brand-blue: #3277b8;
    --brand-blue-light: #4287c4;
    --charcoal: #454545;
    --ink: #2f2f2f;
    --paper: #ffffff;
    --photo-tone: #c9d3dd;
    --backdrop: #222222;
  }
  * { box-sizing: border-box; margin: 0; padding: 0; }
  html, body {
    width: 1200px; height: 900px; overflow: hidden;
    background: var(--backdrop);
    font-family: "Montserrat", sans-serif;
  }
  .canvas { position: relative; width: 1200px; height: 900px; }
  .card {
    position: absolute; left: 250px; width: 700px; height: 400px; overflow: hidden;
  }
  .card--front {
    top: 30px;
    background: linear-gradient(135deg, var(--brand-blue) 0%, var(--brand-blue) 55%, var(--brand-blue-light) 100%);
    display: flex; flex-direction: column; align-items: center; justify-content: center;
  }
  .front-name {
    color: var(--paper); font-weight: 600; font-size: 46px; letter-spacing: 1px;
    text-transform: uppercase; line-height: 1;
  }
  .tagline {
    display: flex; align-items: center; gap: 10px; margin-top: 6px;
    color: var(--charcoal); font-weight: 500; font-size: 15px; letter-spacing: 6px;
    text-transform: uppercase;
  }
  .tagline::before, .tagline::after {
    content: ""; width: 52px; height: 1.5px; background: var(--charcoal);
  }
  .card--back { top: 470px; background: var(--paper); }
  .agent-photo {
    position: absolute; left: 40px; top: 50px; width: 120px; height: 150px;
    background: linear-gradient(180deg, var(--photo-tone), #aebccb);
    border-bottom: 4px solid var(--brand-blue);
  }
  .brand-mark {
    position: absolute; left: 178px; top: 68px; width: 190px;
    color: var(--brand-blue); font-weight: 700; font-size: 44px; line-height: 1.05;
    text-transform: uppercase;
  }
  .details {
    position: absolute; right: 48px; top: 36px; text-align: right;
  }
  .company-name {
    color: var(--brand-blue); font-weight: 600; font-size: 30px; letter-spacing: 0.5px;
    text-transform: uppercase; line-height: 1;
  }
  .details .tagline { justify-content: flex-end; font-size: 12px; letter-spacing: 4px; margin-top: 3px; }
  .details .tagline::before, .details .tagline::after { width: 34px; }
  .agent-name {
    margin-top: 30px; color: var(--brand-blue); font-weight: 600; font-size: 26px;
    letter-spacing: 1px; text-transform: uppercase; line-height: 1.2;
  }
  .agent-title { color: var(--ink); font-size: 17px; margin-top: 2px; }
  .contact-list { list-style: none; margin-top: 20px; }
  .contact-item {
    display: flex; align-items: center; justify-content: flex-end; gap: 12px;
    color: var(--ink); font-size: 17px; line-height: 28px;
  }
  .contact-item svg { width: 16px; height: 16px; flex: none; }
  .swoosh { position: absolute; left: 0; bottom: 0; width: 700px; height: 140px; }
</style>
</head>
<body>
<main class="canvas">
  <section class="card card--front" aria-label="Card front">
    <h1 class="front-name">Maple Gable</h1>
    <p class="tagline">Real Estate</p>
  </section>

  <section class="card card--back" aria-label="Card back">
    <div class="agent-photo" role="img" aria-label="Agent portrait photo"></div>
    <div class="brand-mark">Maple<br>Gable</div>

    <div class="details">
      <h2 class="company-name">Maple Gable</h2>
      <p class="tagline">Real Estate</p>
      <p class="agent-name">Daniel Whitford</p>
      <p class="agent-title">Director</p>
      <ul class="contact-list">
        <li class="contact-item">(555) 214-3086
          <svg viewBox="0 0 16 16" fill="none" stroke="var(--brand-blue)" stroke-width="1.6" stroke-linecap="round" stroke-linejoin="round"><path d="M4 1.5 L6 5 L4.5 6.5 C5.5 9 7 10.5 9.5 11.5 L11 10 L14.5 12 L13 14.5 C7 14 2 9 1.5 3 Z"/></svg>
        </li>
        <li class="contact-item">hello@maplegable.com
          <svg viewBox="0 0 16 16" fill="none" stroke="var(--brand-blue)" stroke-width="1.6" stroke-linejoin="round"><rect x="1.5" y="3.5" width="13" height="9"/><polyline points="1.5,3.5 8,9 14.5,3.5"/></svg>
        </li>
        <li class="contact-item">www.maplegable.com
          <svg viewBox="0 0 16 16" fill="none" stroke="var(--brand-blue)" stroke-width="1.4"><circle cx="8" cy="8" r="6.5"/><ellipse cx="8" cy="8" rx="3" ry="6.5"/><line x1="1.5" y1="8" x2="14.5" y2="8"/><line x1="2.5" y1="4.8" x2="13.5" y2="4.8"/><line x1="2.5" y1="11.2" x2="13.5" y2="11.2"/></svg>
        </li>
        <li class="contact-item">214 Linden Row, Fairview, OR 97024
          <svg viewBox="0 0 16 16" fill="none" stroke="var(--brand-blue)" stroke-width="1.6" stroke-linejoin="round"><path d="M8 15 C4 10.5 3 8.5 3 6.3 A5 5 0 0 1 13 6.3 C13 8.5 12 10.5 8 15 Z"/><circle cx="8" cy="6.3" r="1.8"/></svg>
        </li>
      </ul>
    </div>

    <svg class="swoosh" viewBox="0 0 700 140" preserveAspectRatio="none" aria-hidden="true">
      <path d="M150 140 Q 470 40 700 86 L700 95 Q 480 62 210 140 Z" fill="var(--charcoal)"/>
      <path d="M290 140 Q 520 80 700 100 L700 140 Z" fill="var(--brand-blue)"/>
    </svg>
  </section>
</main>
</body>
</html>
```